Whitcombe Business Card Design

The name of the business is Dario Whitcombe, CPA LLC
The service that we offer is Accounting, Tax & Consulting Services. I need it to have the following items:
Dario Whitcombe, Principal
Phone Number
Email Address
Physical Address

I have attached the company logo, one in black and one in white. Please provide a design in black background and the other in white background. Please include "Accounting, Tax & Consulting Services". I want the business card to be clean and very professional.

```html
<!DOCTYPE html>
<html lang="en">
<head>
<meta charset="utf-8">
<title>Dario Whitcombe, CPA LLC – Business Card</title>
<link rel="stylesheet" href="https://fonts.googleapis.com/css2?family=Montserrat:wght@400;500;600;800&display=swap">
<style>
  :root {
    --stage: #141414;
    --card: #1f1f20;
    --red: #9b1c1f;
    --grey: #6b6b6d;
    --grey-light: #8a8a8c;
    --white: #f2f2f2;
  }
  * { box-sizing: border-box; margin: 0; padding: 0; }
  html, body { width: 1200px; height: 900px; overflow: hidden; }
  body {
    background: var(--stage);
    font-family: "Montserrat", sans-serif;
    display: flex;
    flex-direction: column;
    align-items: center;
    justify-content: center;
    gap: 40px;
  }
  .card {
    position: relative;
    width: 560px;
    height: 320px;
    background: var(--card);
    border-radius: 14px;
    box-shadow: 0 10px 30px rgba(0,0,0,.6);
    overflow: hidden;
  }
  .brand {
    display: flex;
    align-items: center;
    gap: 14px;
  }
  .brand-square {
    width: 34px;
    height: 34px;
    background: var(--red);
    flex: none;
  }
  .brand-name {
    font-weight: 600;
    color: var(--grey-light);
    letter-spacing: 1px;
    text-transform: uppercase;
    white-space: nowrap;
  }
  .brand-tagline {
    font-weight: 500;
    color: var(--grey-light);
    letter-spacing: 2.5px;
    text-transform: uppercase;
    white-space: nowrap;
  }
  /* front */
  .card-front .brand {
    position: absolute;
    left: 70px;
    top: 112px;
  }
  .card-front .brand-name { font-size: 24px; }
  .card-front .brand-tagline { font-size: 15px; margin-top: 4px; }
  .card-front .services {
    font-size: 13px;
    font-weight: 600;
    color: var(--grey);
    margin-top: 10px;
    white-space: nowrap;
  }
  /* back */
  .card-back .brand {
    position: absolute;
    left: 34px;
    bottom: 46px;
    gap: 10px;
  }
  .card-back .brand-square { width: 22px; height: 22px; }
  .card-back .brand-name { font-size: 14px; }
  .card-back .brand-tagline { font-size: 8.5px; letter-spacing: 1.6px; margin-top: 2px; }
  .name-band {
    position: absolute;
    right: 0;
    top: 58px;
    width: 300px;
    height: 40px;
    background: var(--red);
    color: var(--white);
    font-weight: 800;
    font-size: 15px;
    letter-spacing: .3px;
    display: flex;
    align-items: center;
    padding-left: 20px;
    text-transform: uppercase;
  }
  .contact-list {
    position: absolute;
    left: 290px;
    top: 122px;
    list-style: none;
    color: var(--white);
    font-size: 12px;
    line-height: 1.45;
  }
  .contact-list li {
    display: flex;
    align-items: center;
    gap: 12px;
    margin-bottom: 9px;
  }
  .icon {
    width: 20px;
    height: 20px;
    flex: none;
  }
</style>
</head>
<body>

<section class="card card-front" aria-label="Card front">
  <div class="brand">
    <span class="brand-square"></span>
    <div>
      <p class="brand-name">Dario Whitcombe, CPA, LLC</p>
      <p class="brand-tagline">Certified Public Accountant</p>
      <p class="services">Accounting, Tax &amp; Consulting Services</p>
    </div>
  </div>
</section>

<section class="card card-back" aria-label="Card back">
  <div class="brand">
    <span class="brand-square"></span>
    <div>
      <p class="brand-name">Dario Whitcombe, CPA, LLC</p>
      <p class="brand-tagline">Certified Public Accountant</p>
    </div>
  </div>

  <div class="name-band">Dario Whitcombe, Principal</div>

  <ul class="contact-list">
    <li>
      <svg class="icon" viewBox="0 0 20 20" aria-hidden="true">
        <circle cx="10" cy="10" r="10" fill="var(--red)"/>
        <path d="M10 4.5a3.3 3.3 0 0 0-3.3 3.3c0 2.5 3.3 6.7 3.3 6.7s3.3-4.2 3.3-6.7A3.3 3.3 0 0 0 10 4.5z" fill="#fff"/>
        <circle cx="10" cy="7.8" r="1.2" fill="var(--red)"/>
      </svg>
      <span>#27-C, Harlow Court,<br>Linden Avenue, Brookfield, 204118</span>
    </li>
    <li>
      <svg class="icon" viewBox="0 0 20 20" aria-hidden="true">
        <circle cx="10" cy="10" r="10" fill="var(--red)"/>
        <path d="M7 5.5l1.6 0 .8 2.4-1.1.8a6 6 0 0 0 2.9 2.9l.8-1.1 2.4.8v1.6c0 .6-.5 1-1.1 1A8.3 8.3 0 0 1 6 6.6c0-.6.4-1.1 1-1.1z" fill="#fff"/>
      </svg>
      <span>555-214-3097</span>
    </li>
    <li>
      <svg class="icon" viewBox="0 0 20 20" aria-hidden="true">
        <circle cx="10" cy="10" r="10" fill="var(--red)"/>
        <rect x="5" y="6.5" width="10" height="7" fill="#fff"/>
        <path d="M5 6.5l5 4 5-4" fill="none" stroke="var(--red)" stroke-width="1"/>
      </svg>
      <span>info@dariowhitcombecpa.com</span>
    </li>
    <li>
      <svg class="icon" viewBox="0 0 20 20" aria-hidden="true">
        <circle cx="10" cy="10" r="10" fill="var(--red)"/>
        <circle cx="10" cy="10" r="5" fill="none" stroke="#fff" stroke-width="1.2"/>
        <ellipse cx="10" cy="10" rx="2.2" ry="5" fill="none" stroke="#fff" stroke-width="1"/>
        <path d="M5 10h10" stroke="#fff" stroke-width="1"/>
      </svg>
      <span>www.dariowhitcombecpa.com</span>
    </li>
  </ul>
</section>

</body>
</html>
```